Homemaking training schools needs a Business Card design

Designer, Hello!

No special requirements, good-looking enough.
--------------------------------------------------------------------------

Name: Marcus Dole
Chairman
Tel: 0574-71948263
Mobile: 13857420916
Email: kelvora@mailnest.example
Web: www.prt2019.example
Add: No.258, LanpingJie, BeiyuanQu, Ningbo, Zhejiang

LOGO
Ningbo PRT Homemaking Training School

Target Market(s)

pregnant women, mothers, infants, the elderly and families, including cleaning, cooking, nursing training.

Industry/Entity Type

Business

Contact Information for Business Card

Name: Marcus Dole
Chairman
Tel: 0574-71948263
Mobile: 13857420916
Email: kelvora@mailnest.example
Web: www.prt2019.example

LOGO

Font styles to use
Serif
Sans Serif
Decorative

Requirements
Nice to have
• Feels: clean, specifications, safety, comfort, warmth and happiness.

```html
<!DOCTYPE html>
<html lang="en">
<head>
<meta charset="utf-8">
<title>PeiRuiTang Business Card</title>
<link rel="stylesheet" href="https://fonts.googleapis.com/css2?family=Questrial&family=Lato:wght@400;700&display=swap">
<style>
  :root {
    --stage: #2e2e2e;
    --brand-blue: #3878b8;
    --brand-pink: #dc0c86;
    --paper: #ffffff;
    --ink-dark: #1f1f1f;
  }
  * { box-sizing: border-box; margin: 0; padding: 0; }
  html, body { width: 1200px; height: 1166px; overflow: hidden; }
  body {
    background: var(--stage);
    font-family: "Lato", sans-serif;
    position: relative;
  }
  .card {
    position: absolute;
    left: 180px;
    width: 840px;
    height: 504px;
    overflow: hidden;
    box-shadow: 0 20px 40px rgba(0,0,0,.45);
  }
  .card--front { top: 50px; background: var(--brand-blue); }
  .card--back { top: 600px; background: var(--brand-blue); }
  .card__shapes { position: absolute; inset: 0; }

  .wordmark { position: absolute; display: flex; flex-direction: column; }
  .wordmark__row { display: flex; align-items: center; gap: 14px; }
  .wordmark__dot {
    width: 26px; height: 26px; border-radius: 50%;
    background: var(--brand-pink); flex: none;
  }
  .wordmark__name {
    font-family: "Questrial", sans-serif;
    font-size: 64px; line-height: 1; letter-spacing: -1px;
  }
  .wordmark__tagline {
    display: flex; align-items: center; gap: 12px;
    font-family: "Questrial", sans-serif;
    font-size: 22px; margin-top: 8px;
  }
  .wordmark__rule { height: 1.5px; flex: 1; }

  .card--front .wordmark { left: 200px; top: 170px; width: 460px; color: var(--paper); }
  .card--front .wordmark__rule { background: var(--paper); }
  .front__web {
    position: absolute; left: 0; right: 0; top: 330px;
    text-align: center; color: var(--paper);
    font-size: 17px; letter-spacing: 3px;
  }

  .card--back .wordmark { left: 70px; top: 120px; width: 420px; color: var(--brand-blue); }
  .card--back .wordmark__tagline { color: var(--ink-dark); }
  .card--back .wordmark__rule { background: var(--ink-dark); }
  .card--back .wordmark__name { font-size: 58px; }

  .holder {
    position: absolute; right: 40px; top: 222px;
    color: var(--paper); text-align: right;
    font-family: "Questrial", sans-serif;
  }
  .holder__name { font-size: 30px; line-height: 1.1; }
  .holder__title { font-size: 18px; }

  .contact {
    position: absolute; left: 70px; top: 345px;
    color: var(--paper); font-size: 19px; line-height: 1.3;
  }
  .contact__address { margin-bottom: 6px; }
  .contact__list { list-style: none; }
  .contact__item { display: flex; align-items: center; gap: 12px; }
  .contact__icon { width: 16px; height: 16px; flex: none; }
</style>
</head>
<body>

  <section class="card card--front" aria-label="Card front">
    <div class="wordmark">
      <div class="wordmark__row">
        <span class="wordmark__dot"></span>
        <span class="wordmark__name">PeiRuiTang</span>
      </div>
      <div class="wordmark__tagline">
        <span class="wordmark__rule"></span>
        <span>Training &amp; Services</span>
        <span class="wordmark__rule"></span>
      </div>
    </div>
    <p class="front__web">www.prt2019.example</p>
  </section>

  <section class="card card--back" aria-label="Card back">
    <svg class="card__shapes" viewBox="0 0 840 504" width="840" height="504" aria-hidden="true">
      <path d="M0 0 H840 V205 H560 L500 300 H0 Z" fill="var(--paper)"/>
      <path d="M0 300 H500 L560 205 H840 V290 H700 L660 322 H0 Z" fill="var(--brand-pink)"/>
      <path d="M0 326 H662 L702 295 H840" fill="none" stroke="var(--paper)" stroke-width="3"/>
    </svg>

    <div class="wordmark">
      <div class="wordmark__row">
        <span class="wordmark__dot"></span>
        <span class="wordmark__name">PeiRuiTang</span>
      </div>
      <div class="wordmark__tagline">
        <span class="wordmark__rule"></span>
        <span>Training &amp; Services</span>
        <span class="wordmark__rule"></span>
      </div>
    </div>

    <div class="holder">
      <p class="holder__name">Marcus Dole</p>
      <p class="holder__title">Chairman</p>
    </div>

    <div class="contact">
      <p class="contact__address">No.258, LanpingJie<br>BeiyuanQu, Ningbo, Zhejiang</p>
      <ul class="contact__list">
        <li class="contact__item">
          <svg class="contact__icon" viewBox="0 0 16 16" aria-hidden="true"><path d="M3 1 L6 1 L7 5 L5 6 Q6 9 10 11 L11 9 L15 10 L15 13 Q15 15 13 15 Q2 14 1 3 Q1 1 3 1Z" fill="var(--brand-pink)"/></svg>
          <span>0574-71948263</span>
        </li>
        <li class="contact__item">
          <svg class="contact__icon" viewBox="0 0 16 16" aria-hidden="true"><rect x="4" y="1" width="8" height="14" rx="1.5" fill="none" stroke="var(--brand-pink)" stroke-width="1.6"/><circle cx="8" cy="12.5" r="1" fill="var(--brand-pink)"/></svg>
          <span>1385-7420916</span>
        </li>
        <li class="contact__item">
          <svg class="contact__icon" viewBox="0 0 16 16" aria-hidden="true"><rect x="1" y="3" width="14" height="10" fill="var(--brand-pink)"/><path d="M1 3 L8 9 L15 3" fill="none" stroke="var(--brand-blue)" stroke-width="1.2"/></svg>
          <span>kelvora@mailnest.example</span>
        </li>
        <li class="contact__item">
          <svg class="contact__icon" viewBox="0 0 16 16" aria-hidden="true"><g fill="none" stroke="var(--brand-pink)" stroke-width="1.4"><circle cx="8" cy="8" r="6.5"/><ellipse cx="8" cy="8" rx="3" ry="6.5"/><path d="M1.5 8 H14.5 M2.5 5 H13.5 M2.5 11 H13.5"/></g></svg>
          <span>www.prt2019.example</span>
        </li>
      </ul>
    </div>
  </section>

</body>
</html>
```